Progressive Flow Chart

Looking for a progressive flow chart centered and branching off. They all build on each other 1-3. There will be 3 different pages.

Target Market(s)

Business Owners - High Net worth Individuals

Industry/Entity Type

Finance & Business Consulting

Font styles to use
Serif

Colors
0054AA
0677BA
7BADD7
CADEEF
E8F1F8
0094D4
00A9DD
6FCCEA
C7EBF8
E9F6FB
00AB8E
00BBA5
67D7C9
C6EFE9
E9F9F6

Requirements
Nice to have
• Clean, simple, and approachable.
Should not have
• Very Busy

```html
<!DOCTYPE html>
<html lang="en">
<head>
<meta charset="utf-8">
<title>Progressive Flow Chart</title>
<link rel="stylesheet" href="https://fonts.googleapis.com/css2?family=Jost:wght@400;600;700&display=swap">
<style>
  :root {
    --page: #b5b5b5;
    --navy: #0b1338;
    --panel: #1d2452;
    --white: #ffffff;
    --ink: #0b1338;
    --mint: #12f0b4;
    --blue: #2aa3e4;
    --line: #3ab4ea;
    --muted: #6f86c7;
  }
  * { margin: 0; padding: 0; box-sizing: border-box; }
  html, body { width: 1200px; height: 1200px; overflow: hidden; background: var(--page); }
  .chart { position: absolute; left: 0; top: 176px; width: 1200px; height: 848px; display: block; }
  .chart text { font-family: "Jost", sans-serif; }
  .node-title { font-weight: 700; fill: var(--mint); text-anchor: middle; }
  .node-note { font-weight: 600; fill: var(--white); text-anchor: middle; font-size: 19px; }
  .white-title { font-weight: 700; fill: var(--ink); text-anchor: middle; font-size: 30px; }
  .badge-num { font-weight: 700; fill: var(--ink); text-anchor: middle; font-size: 24px; }
  .flow-label { font-weight: 400; fill: var(--white); font-size: 15px; text-anchor: middle; letter-spacing: .5px; }
  .flow { stroke: var(--line); stroke-width: 3; stroke-dasharray: 2 6; stroke-linecap: round; fill: none; }
  .brand-name { font-weight: 600; fill: var(--blue); text-anchor: middle; font-size: 34px; }
</style>
</head>
<body>
<svg class="chart" viewBox="0 0 1675 1184" xmlns="http://www.w3.org/2000/svg">
  <defs>
    <linearGradient id="ring" x1="0" y1="0" x2="1" y2="0">
      <stop offset="0" stop-color="#2aa3e4"/>
      <stop offset="1" stop-color="#00f5b0"/>
    </linearGradient>
    <radialGradient id="glow-left" cx="0.1" cy="0.2" r="0.55">
      <stop offset="0" stop-color="#1a3a8a" stop-opacity=".55"/>
      <stop offset="1" stop-color="#0b1338" stop-opacity="0"/>
    </radialGradient>
    <radialGradient id="glow-right" cx="0.95" cy="0.9" r="0.4">
      <stop offset="0" stop-color="#1a3a8a" stop-opacity=".45"/>
      <stop offset="1" stop-color="#0b1338" stop-opacity="0"/>
    </radialGradient>
    <marker id="head" viewBox="0 0 10 10" refX="5" refY="5" markerWidth="9" markerHeight="9" orient="auto-start-reverse">
      <path d="M0 0 L10 5 L0 10 L3 5 Z" fill="#19d6c8"/>
    </marker>
  </defs>

  <rect class="board" width="1675" height="1184" fill="var(--navy)"/>
  <rect class="board-texture" width="1675" height="1184" fill="url(#glow-left)" role="img" aria-label="Soft dotted wave pattern"/>
  <rect class="board-texture" width="1675" height="1184" fill="url(#glow-right)" role="img" aria-label="Soft dotted wave pattern"/>

  <!-- brand panel -->
  <path class="brand-panel" d="M1412 364 H1675 V784 H1412 A210 210 0 0 1 1412 364 Z" fill="var(--panel)"/>
  <circle cx="1427" cy="545" r="16" fill="var(--blue)"/>
  <text class="brand-name" x="1427" y="640">Harbor Crest</text>
  <text x="1427" y="682" text-anchor="middle" font-size="15" letter-spacing="4" fill="var(--muted)">FINANCIAL</text>

  <!-- flows -->
  <line class="flow" x1="340" y1="204" x2="750" y2="204"/>
  <line class="flow" x1="935" y1="204" x2="1330" y2="204"/>
  <line class="flow" x1="376" y1="502" x2="450" y2="502"/>
  <line class="flow" x1="555" y1="502" x2="650" y2="502"/>
  <line class="flow" x1="213" y1="845" x2="213" y2="780"/>
  <line class="flow" x1="213" y1="680" x2="213" y2="620" marker-end="url(#head)"/>
  <line class="flow" x1="277" y1="845" x2="277" y2="620"/>
  <line class="flow" x1="282" y1="846" x2="430" y2="780" marker-end="url(#head)"/>
  <line class="flow" x1="480" y1="760" x2="660" y2="680" marker-end="url(#head)"/>
  <line class="flow" x1="282" y1="617" x2="660" y2="758" marker-end="url(#head)"/>
  <line class="flow" x1="660" y1="758" x2="850" y2="836"/>
  <line class="flow" x1="850" y1="836" x2="850" y2="830"/>
  <line class="flow" x1="850" y1="800" x2="850" y2="780" marker-end="url(#head)"/>
  <line class="flow" x1="385" y1="966" x2="510" y2="966"/>
  <line class="flow" x1="580" y1="966" x2="730" y2="966"/>
  <line class="flow" x1="1017" y1="719" x2="1210" y2="790" marker-end="url(#head)"/>
  <line class="flow" x1="1210" y1="790" x2="1360" y2="846"/>
  <line class="flow" x1="1297" y1="874" x2="1100" y2="804" marker-end="url(#head)"/>
  <line class="flow" x1="1100" y1="804" x2="972" y2="754"/>

  <text class="flow-label" x="511" y="508">INVESTS</text>
  <text class="flow-label" x="544" y="971">RENT</text>
  <text class="flow-label" x="850" y="816">INCOME</text>
  <text class="flow-label" transform="translate(452 818) rotate(-24)">INCOME</text>
  <text class="flow-label" transform="translate(218 732) rotate(-90)">INTEREST</text>
  <text class="flow-label" transform="translate(282 732) rotate(-90)">INVESTMENTS</text>

  <!-- level 3 -->
  <g class="node node-white">
    <circle cx="245" cy="204" r="76" fill="var(--white)" stroke="url(#ring)" stroke-width="14"/>
    <text class="white-title" x="245" y="215">CRT</text>
  </g>
  <g class="node node-white">
    <circle cx="842" cy="204" r="76" fill="var(--white)" stroke="url(#ring)" stroke-width="14"/>
    <text class="white-title" x="845" y="215">DAF</text>
  </g>
  <g class="node node-white">
    <circle cx="1425" cy="204" r="76" fill="var(--white)" stroke="url(#ring)" stroke-width="14"/>
    <text class="white-title" x="1427" y="200">GRATS’</text>
    <text class="white-title" x="1427" y="230">IDGT’S</text>
  </g>

  <!-- living trust -->
  <g class="node node-trust">
    <path d="M670 424 A245 245 0 0 1 1030 424" fill="none" stroke="url(#ring)" stroke-width="32" stroke-linecap="round"/>
    <circle cx="850" cy="569" r="168" fill="none" stroke="url(#ring)" stroke-width="84"/>
    <circle cx="850" cy="569" r="126" fill="var(--navy)" stroke="#12355e" stroke-width="14"/>
    <text x="850" y="424" text-anchor="middle" font-weight="700" font-size="24" fill="var(--ink)">LIVING TRUST</text>
    <text class="node-title" x="850" y="567" font-size="40">YOU</text>
    <text x="850" y="606" text-anchor="middle" font-weight="700" font-size="40" fill="var(--white)">TRUSTEE</text>
  </g>

  <!-- level 1/2 rings -->
  <g class="node">
    <circle cx="245" cy="497" r="108" fill="var(--navy)" stroke="url(#ring)" stroke-width="14"/>
    <text class="node-title" x="245" y="466" font-size="30">BANK</text>
    <text class="node-note" x="245" y="494">MAKES</text>
    <text class="node-note" x="245" y="517">INVESTMENTS TO</text>
    <text class="node-note" x="245" y="539">REAL ESTATES +</text>
    <text class="node-note" x="245" y="561">BUSINESS</text>
  </g>
  <g class="node">
    <circle cx="245" cy="964" r="108" fill="var(--navy)" stroke="url(#ring)" stroke-width="14"/>
    <text class="node-title" x="245" y="970" font-size="27">REAL ESTATE</text>
    <text class="node-title" x="245" y="1000" font-size="27">LLC</text>
  </g>
  <g class="node">
    <circle cx="850" cy="964" r="108" fill="var(--navy)" stroke="url(#ring)" stroke-width="14"/>
    <text class="node-title" x="852" y="954" font-size="26">BUSINESS LLC</text>
    <text class="node-note" x="852" y="984">MEMBER/MANAGER</text>
    <text class="node-note" x="852" y="1009">CORP=PRESIDENT</text>
  </g>
  <g class="node">
    <circle cx="1399" cy="964" r="108" fill="var(--navy)" stroke="url(#ring)" stroke-width="14"/>
    <text class="node-title" x="1399" y="976" font-size="27">INSURANCE</text>
  </g>

  <!-- step badges -->
  <g class="badges" fill="var(--white)" stroke="#2aa3e4" stroke-width="3">
    <circle cx="186" cy="145" r="21"/><circle cx="789" cy="145" r="21"/><circle cx="1373" cy="145" r="21"/>
    <circle cx="171" cy="420" r="21"/><circle cx="775" cy="472" r="21"/>
    <circle cx="171" cy="886" r="21"/><circle cx="775" cy="886" r="21"/><circle cx="1320" cy="886" r="21"/>
  </g>
  <g>
    <text class="badge-num" x="186" y="154">3</text>
    <text class="badge-num" x="789" y="154">3</text>
    <text class="badge-num" x="1373" y="154">3</text>
    <text class="badge-num" x="171" y="429">2</text>
    <text class="badge-num" x="775" y="481">1</text>
    <text class="badge-num" x="171" y="895">1</text>
    <text class="badge-num" x="775" y="895">1</text>
    <text class="badge-num" x="1320" y="895">2</text>
  </g>
</svg>
</body>
</html>
```